VELMOR Website Design

We need a website designed for our company VELMOR. We are a luxury lifestyle club that will provide benefits and services for our members. The site should be clean & sleek, preferably using black and white (or darker colors). (example sites: stravenhall.example, plinth.example)

Here is a link of a sample page I did using wix. (https://dunmere7.sitehostly.example/mysite) This can be used to get a general idea.

Target Market(s)

Upper Middle Class in the United States

Number of Pages Required

5+ page

Font styles to use
Sans Serif
Other font styles liked:
• Arial (or other similar fonts)

Requirements
Must have
• A clean design that is eye-catching and speaks to our company.
Nice to have
• Ideas for copy.

```html
<!DOCTYPE html>
<html lang="en">
<head>
<meta charset="utf-8">
<title>VELMOR — A Members Only Lifestyle Club</title>
<link rel="stylesheet" href="https://fonts.googleapis.com/css2?family=Lato:wght@300;400;700;900&display=swap">
<style>
  :root {
    --ink: #1b1b1b;
    --night: #1e1e1e;
    --night-card: #232323;
    --paper: #ffffff;
    --line: #8a8a8a;
    --muted: #555555;
    --soft: #bdbdbd;
    --white: #ffffff;
  }
  * { box-sizing: border-box; margin: 0; padding: 0; }
  html, body { width: 1200px; height: 2580px; overflow: hidden; }
  body { font-family: "Lato", Arial, sans-serif; background: var(--paper); color: var(--ink); position: relative; }

  .hero { position: absolute; left: 0; top: 0; width: 1200px; height: 680px;
    background: linear-gradient(160deg, #2f4a55 0%, #1f2a30 35%, #3a3029 60%, #121416 100%); }
  .hero-shade { position: absolute; inset: 0; background: rgba(0,0,0,0.28); }
  .site-header { position: absolute; left: 0; top: 0; width: 1200px; height: 88px;
    background: rgba(0,0,0,0.35); display: flex; align-items: center; padding: 0 140px 0 136px; }
  .brand { color: var(--white); font-weight: 400; font-size: 34px; letter-spacing: 2px; }
  .main-nav { margin-left: 64px; display: flex; gap: 34px; }
  .main-nav a { color: var(--white); text-decoration: none; font-size: 14px; letter-spacing: 1px; }
  .hero-copy { position: absolute; left: 0; top: 244px; width: 1200px; text-align: center; color: var(--white); }
  .hero-title { font-weight: 900; font-size: 46px; letter-spacing: 1px; }
  .hero-sub { margin-top: 18px; font-weight: 700; font-size: 25px; line-height: 32px; letter-spacing: 1px; }
  .btn { display: inline-block; border: 2px solid currentColor; padding: 8px 22px; font-size: 15px;
    font-weight: 700; letter-spacing: 1px; text-decoration: none; }
  .hero .btn { margin-top: 28px; color: var(--white); background: rgba(0,0,0,0.3); }
  .arrow { position: absolute; width: 30px; height: 50px; }
  .scroll-notch { position: absolute; left: 540px; top: 640px; width: 120px; height: 60px; }

  .about { position: absolute; left: 0; top: 680px; width: 1200px; height: 330px; text-align: center; }
  .section-title { font-weight: 700; font-size: 38px; letter-spacing: 3px; }
  .about .section-title { margin-top: 86px; }
  .about p { width: 760px; margin: 22px auto 0; font-size: 19px; line-height: 26px; color: var(--muted); }
  .about .btn { margin-top: 26px; color: var(--ink); }
  .jet-photo { position: absolute; left: 0; top: 1010px; width: 1200px; height: 372px;
    background: linear-gradient(180deg, #cfd3d6 0%, #e6e7e8 55%, #8d8f91 100%); }

  .services { position: absolute; left: 0; top: 1382px; width: 1200px; height: 530px; background: var(--night); color: var(--white); }
  .services .section-title { position: absolute; top: 60px; width: 1200px; text-align: center; font-size: 32px; letter-spacing: 5px; }
  .services .rule { position: absolute; top: 112px; left: 0; width: 1200px; height: 1px; background: #3a3a3a; }
  .card { position: absolute; top: 132px; width: 290px; height: 285px; border: 1px solid var(--line);
    background: var(--night-card); text-align: center; padding-top: 26px; }
  .card svg { width: 60px; height: 60px; }
  .card h3 { margin-top: 10px; font-size: 20px; font-weight: 700; }
  .card p { width: 220px; margin: 16px auto 0; font-size: 12px; line-height: 17px; color: var(--soft); }
  .card .btn { margin-top: 24px; background: var(--white); color: var(--ink); border-color: var(--white); font-size: 12px; padding: 6px 16px; }

  .experiences { position: absolute; left: 0; top: 1912px; width: 1200px; height: 490px;
    background: linear-gradient(120deg, #2c211b 0%, #5a4030 45%, #2a1f19 80%, #1a1512 100%); }
  .exp-box { position: absolute; left: 312px; top: 200px; width: 576px; height: 190px;
    background: rgba(40,40,40,0.55); border: 2px solid rgba(255,255,255,0.6); text-align: center; color: var(--white); }
  .exp-box .section-title { margin-top: 26px; font-size: 32px; letter-spacing: 5px; }
  .exp-box p { width: 440px; margin: 14px auto 0; font-size: 15px; line-height: 24px; }

  .site-footer { position: absolute; left: 0; top: 2402px; width: 1200px; height: 178px; text-align: center; }
  .socials { margin-top: 22px; display: flex; justify-content: center; gap: 12px; }
  .socials span { width: 40px; height: 40px; border: 2px solid var(--ink); border-radius: 50%; }
  .footer-nav { margin-top: 28px; display: flex; justify-content: center; gap: 30px; }
  .footer-nav a { color: var(--ink); text-decoration: none; font-size: 15px; letter-spacing: 1px; }
  .copyright { margin-top: 16px; font-size: 11px; letter-spacing: 1px; color: var(--muted); }
</style>
</head>
<body>

<section class="hero">
  <div class="hero-photo" role="img" aria-label="Photograph of a woman in a swimsuit and sun hat lounging beside a pool" style="position:absolute;inset:0;"></div>
  <div class="hero-shade"></div>
  <header class="site-header">
    <div class="brand">VELMOR</div>
    <nav class="main-nav">
      <a href="#">HOME</a><a href="#">ABOUT US</a><a href="#">SERVICES &amp; BENEFITS</a><a href="#">MORE</a><a href="#">CONTACT US</a>
    </nav>
  </header>
  <div class="hero-copy">
    <h1 class="hero-title">A MEMBERS ONLY LIFESTYLE CLUB</h1>
    <p class="hero-sub">VELMOR MEMBERSHIP PROVIDES YOU WITH<br>AMAZING BENEFITS AND SERVICES</p>
    <a class="btn" href="#">READ MORE</a>
  </div>
  <svg class="arrow" style="left:80px;top:322px" viewBox="0 0 30 50"><polyline points="24,4 6,25 24,46" fill="none" stroke="#fff" stroke-width="3"/></svg>
  <svg class="arrow" style="left:1090px;top:322px" viewBox="0 0 30 50"><polyline points="6,4 24,25 6,46" fill="none" stroke="#fff" stroke-width="3"/></svg>
  <svg class="scroll-notch" viewBox="0 0 120 60" aria-hidden="true">
    <path d="M0 40 Q30 40 40 20 Q60 -8 80 20 Q90 40 120 40 L120 60 L0 60 Z" fill="#fff"/>
    <rect x="52" y="14" width="16" height="26" rx="8" fill="none" stroke="#555" stroke-width="2"/>
    <line x1="60" y1="19" x2="60" y2="25" stroke="#555" stroke-width="2"/>
  </svg>
</section>

<section class="about">
  <h2 class="section-title">ABOUT VELMOR</h2>
  <p>VELMOR was formed to bring the best services, experiences, and exclusive opportunities to our members. With everything from private member events to private jet travel, the perks of being a VELMOR member are unmatched.</p>
  <a class="btn" href="#">READ MORE</a>
</section>
<div class="jet-photo" role="img" aria-label="Photograph of business travellers walking from a private jet on the tarmac"></div>

<section class="services">
  <h2 class="section-title">SERVICES &amp; BENEFITS</h2>
  <div class="rule"></div>
  <svg class="arrow" style="left:80px;top:250px" viewBox="0 0 30 50"><polyline points="24,4 6,25 24,46" fill="none" stroke="#aaa" stroke-width="3"/></svg>
  <svg class="arrow" style="left:1090px;top:250px" viewBox="0 0 30 50"><polyline points="6,4 24,25 6,46" fill="none" stroke="#aaa" stroke-width="3"/></svg>

  <article class="card" style="left:144px">
    <svg viewBox="0 0 60 60" aria-hidden="true"><rect x="14" y="6" width="32" height="48" rx="2" fill="none" stroke="#fff" stroke-width="3"/><rect x="19" y="11" width="22" height="10" fill="#fff"/><g fill="#fff"><rect x="19" y="26" width="5" height="5"/><rect x="27.5" y="26" width="5" height="5"/><rect x="36" y="26" width="5" height="5"/><rect x="19" y="35" width="5" height="5"/><rect x="27.5" y="35" width="5" height="5"/><rect x="36" y="35" width="5" height="5"/><rect x="19" y="44" width="5" height="5"/><rect x="27.5" y="44" width="5" height="5"/><rect x="36" y="44" width="5" height="5"/></g></svg>
    <h3>Accounting Service</h3>
    <p>Discreet tax planning and bookkeeping from advisors who understand private wealth.</p>
    <a class="btn" href="#">READ MORE</a>
  </article>

  <article class="card" style="left:455px">
    <svg viewBox="0 0 60 60" aria-hidden="true" fill="none" stroke="#fff" stroke-width="3"><path d="M12 10 L26 14 L22 30 Q16 32 12 28 Z"/><line x1="19" y1="31" x2="15" y2="50"/><line x1="9" y1="50" x2="21" y2="52"/><path d="M48 10 L34 14 L38 30 Q44 32 48 28 Z"/><line x1="41" y1="31" x2="45" y2="50"/><line x1="39" y1="52" x2="51" y2="50"/></svg>
    <h3>Private Events</h3>
    <p>Invitations to members-only evenings, tastings and premieres hosted in exceptional venues.</p>
    <a class="btn" href="#">READ MORE</a>
  </article>

  <article class="card" style="left:766px">
    <svg viewBox="0 0 60 60" aria-hidden="true" fill="none" stroke="#fff" stroke-width="3" stroke-linejoin="round"><path d="M30 6 Q34 6 34 14 L34 24 L54 34 L54 38 L34 32 L34 46 L40 51 L40 54 L30 51 L20 54 L20 51 L26 46 L26 32 L6 38 L6 34 L26 24 L26 14 Q26 6 30 6 Z"/></svg>
    <h3>Private Jet</h3>
    <p>Charter flights arranged on short notice with crews vetted for comfort and privacy.</p>
    <a class="btn" href="#">READ MORE</a>
  </article>
</section>

<section class="experiences" role="img" aria-label="Photograph of friends raising champagne glasses at a celebration">
  <div class="exp-box">
    <h2 class="section-title">EXPERIENCES</h2>
    <p>VELMOR engages and supports a host of private events and parties for our members. Members are also provided access to exclusive venues and events from our partners.</p>
  </div>
</section>

<footer class="site-footer">
  <div class="socials" aria-label="Social links"><span></span><span></span><span></span><span></span></div>
  <nav class="footer-nav">
    <a href="#">HOME</a><a href="#">ABOUT US</a><a href="#">SERVICES &amp; BENEFITS</a><a href="#">MORE</a><a href="#">CONTACT US</a>
  </nav>
  <p class="copyright">© 2016 VELMOR. ALL RIGHTS RESERVED</p>
</footer>

</body>
</html>
```